New business card for a regional office of a US M&A company

We need business card for a finance company, office based in Hong Kong , our Head office is in US, our business is to Merge and acquires companies , the new office will be a regional office for the Asia Pacific region. We want to use the head office logo as attached ( but don't have to be exactly the same, can be a variation to it) as a base and then add Asia Pacific alongside the logo.
We would prefer to have be bilingual Eng + Chinese, although we don't really have Chinese company name .

Industry/Entity Type

Business

Contact Information for Business Card

Clara Jo Tsang
 

VP,
APAC M&A Operations
Orin Vantage Asia Pacific Limited
 
Unit 1407, K18
18 Tai Lok Shan Road, 
Hong Kong 
 
M: +852 6038 1742
T : +852 2836 4100
F : +852 2836 4177
VOIP: 4158
 
cjtsang@orinvantage.com

Font styles to use
Serif
Sans Serif

Colors

Designer to choose colors to be used in the design.

Requirements
Must have
• APAC Office

```html
<!DOCTYPE html>
<html lang="en">
<head>
<meta charset="utf-8">
<title>Orin Vantage – APAC Business Card</title>
<link href="https://fonts.googleapis.com/css2?family=Ubuntu:wght@400;500;700&family=Ubuntu+Condensed&display=swap" rel="stylesheet">
<style>
  :root {
    --page: #e4e4e4;
    --navy: #0f2740;
    --brand-blue: #2aa2c8;
    --band-blue: #1f9cc0;
    --text-light: #e8eef3;
    --silver-a: #f2f2f2;
    --silver-b: #a9adb1;
  }
  * { margin: 0; padding: 0; box-sizing: border-box; }
  html, body { width: 1200px; height: 576px; overflow: hidden; }
  body { background: var(--page); position: relative; font-family: "Ubuntu", sans-serif; }

  .card {
    position: absolute;
    width: 484px; height: 293px;
    background: var(--navy);
    border-radius: 12px;
    overflow: hidden;
    box-shadow: 0 3px 8px rgba(0,0,0,0.25);
  }
  .card--front { left: 82px; top: 138px; }
  .card--back  { left: 602px; top: 138px; }

  /* front */
  .front-band { position: absolute; left: 0; right: 0; bottom: 0; height: 7px; background: var(--band-blue); }
  .front-brand {
    position: absolute; left: 0; right: 0; top: 150px;
    display: flex; align-items: center; justify-content: center; gap: 12px;
  }
  .brand-mark { width: 20px; height: 20px; background: var(--brand-blue); }
  .brand-name {
    font-weight: 700; color: var(--brand-blue); letter-spacing: 1px; line-height: 1;
  }
  .front-brand .brand-name { font-size: 36px; }

  /* back */
  .back-brand {
    position: absolute; left: 26px; top: 52px;
    display: flex; align-items: center; gap: 12px;
  }
  .back-brand .brand-mark { width: 26px; height: 26px; }
  .back-brand .brand-name { font-size: 35px; }

  .person { position: absolute; left: 27px; top: 157px; color: var(--text-light); }
  .person__name { font-family: "Ubuntu Condensed", sans-serif; font-size: 19px; color: var(--brand-blue); margin-bottom: 6px; }
  .person__title { font-size: 12px; line-height: 15px; }
  .person__contacts { margin-top: 18px; font-size: 12px; line-height: 15px; }

  .office { position: absolute; left: 239px; top: 161px; color: var(--text-light); font-size: 12px; line-height: 15px; }
  .office__name { font-size: 13.5px; font-weight: 700; color: var(--brand-blue); margin-bottom: 8px; }
  .office__phones { padding-left: 12px; }
  .office__address { margin-top: 4px; padding-left: 10px; }

  .contact { display: flex; align-items: center; gap: 9px; }
  .contact svg { width: 10px; height: 10px; fill: var(--brand-blue); flex: none; }

  .back-footer { position: absolute; left: 0; bottom: 0; width: 484px; height: 32px; }
  .website {
    position: absolute; left: 249px; bottom: 10px;
    font-size: 12px; color: var(--text-light); letter-spacing: 0.6px;
  }
</style>
</head>
<body>

  <section class="card card--front" aria-label="Card front">
    <div class="front-brand">
      <span class="brand-mark"></span>
      <span class="brand-name">ORIN VANTAGE</span>
    </div>
    <div class="front-band"></div>
  </section>

  <section class="card card--back" aria-label="Card back">
    <div class="back-brand">
      <span class="brand-mark"></span>
      <span class="brand-name">ORIN VANTAGE</span>
    </div>

    <div class="person">
      <p class="person__name">Clara Jo Tsang</p>
      <p class="person__title">Vice President,<br>APAC M&amp;A Operations</p>
      <div class="person__contacts">
        <p class="contact">
          <svg viewBox="0 0 10 10"><path d="M2.5 0h5a1 1 0 0 1 1 1v8a1 1 0 0 1-1 1h-5a1 1 0 0 1-1-1V1a1 1 0 0 1 1-1zM3 1.5v6h4v-6z"/></svg>
          +852 6038 1742
        </p>
        <p class="contact">
          <svg viewBox="0 0 10 10"><path d="M0 2h10v6H0zM1 3v.4l4 2.4 4-2.4V3L5 5.3z"/></svg>
          cjtsang@orinvantage.com
        </p>
      </div>
    </div>

    <div class="office">
      <p class="office__name">Orin Vantage Asia Pacific Limited</p>
      <div class="office__phones">
        <p class="contact">
          <svg viewBox="0 0 10 10"><path d="M0 3.5C1 1.5 9 1.5 10 3.5L8.5 4.8 7 4V3H3v1L1.5 4.8zM2 5.5h6L9 9H1z"/></svg>
          +852 2836 4100
        </p>
        <p class="contact">
          <svg viewBox="0 0 10 10"><path d="M2.5 0h5v3h-5zM0 3.5h10V7H8v3H2V7H0zM3 6v3h4V6z"/></svg>
          +852 2836 4177,&nbsp; VOIP: 4158
        </p>
      </div>
      <p class="office__address">Unit 1407, K18 18, Tai Lok Shan<br>Road, Hong Kong</p>
    </div>

    <svg class="back-footer" viewBox="0 0 484 32" preserveAspectRatio="none" aria-hidden="true">
      <defs>
        <linearGradient id="silver" x1="0" x2="1" y1="0" y2="0">
          <stop offset="0" stop-color="var(--silver-b)"/>
          <stop offset="0.5" stop-color="var(--silver-a)"/>
          <stop offset="1" stop-color="var(--silver-b)"/>
        </linearGradient>
      </defs>
      <rect x="0" y="18" width="260" height="14" fill="url(#silver)"/>
      <polygon points="214,2 484,2 484,32 202,32" fill="var(--band-blue)"/>
    </svg>
    <p class="website">www.orinvantage.com</p>
  </section>

</body>
</html>
```